Residential building / Apartments for sale landing page

I need a website / landing page design for my latest development project - a residential building with 70+ apartments for sale. I need the design in layers in Photoshop/Illustrator/InDesign format with all the icons/shapes/maps/graphic assets in vector format (svg, ai, eps) as much as possible.

I prefer white website and please consider the performance/coding experience. We're not making something suitable only for a design contest with fancy parallax effects and confusing animations. We're trying to create usable and clean UI with good UX.

The website will be custom coded, i.e. I'm not using WordPress.

I know that the existing 3D photos are not good but for now you can use them or replace them with some stock photos. I'm going to create new 3D photos soon.

Real Estate Development

1 page

```html
<!DOCTYPE html>
<html lang="en">
<head>
<meta charset="utf-8">
<title>Green Crest – Apartments for Sale</title>
<link href="https://fonts.googleapis.com/css2?family=Poppins:wght@300;400;500;600;700&display=swap" rel="stylesheet">
<style>
:root{
  --green:#8dc63f;
  --dark:#231f20;
  --ink:#1d1d1d;
  --muted:#6b6b6b;
  --light:#f0f0f0;
  --line:#e4e4e4;
  --white:#ffffff;
}
*{margin:0;padding:0;box-sizing:border-box}
html,body{width:1200px;height:4468px;overflow:hidden}
body{font-family:'Poppins',sans-serif;color:var(--ink);background:var(--white);position:relative}
.brand{display:flex;align-items:center;gap:10px;font-weight:700;color:var(--ink);letter-spacing:1px}
.brand .mark{width:18px;height:18px;background:var(--green)}

/* header */
.site-header{position:absolute;left:0;top:0;width:1200px;height:94px;background:var(--white)}
.site-header .brand{position:absolute;left:88px;top:34px;font-size:22px;line-height:26px}
.main-nav{position:absolute;left:372px;top:34px;display:flex;gap:26px;align-items:center;font-size:12px;font-weight:500;text-transform:uppercase}
.main-nav .cta{background:#ececec;padding:7px 16px}
.main-nav .lang{display:flex;align-items:center;gap:6px}
.main-nav .lang i{width:16px;height:16px;border-radius:50%;background:#c9d3e6;display:block}

/* hero */
.hero{position:absolute;left:0;top:94px;width:1200px;height:622px;background:var(--light);overflow:hidden}
.hero .accent{position:absolute;left:775px;top:0;width:425px;height:280px;background:var(--green)}
.hero .photo{position:absolute;left:640px;top:40px;width:560px;height:582px;background:linear-gradient(160deg,#e9ece6,#cfd6c8 55%,#7ea85a)}
.hero h1{position:absolute;left:88px;top:156px;font-size:47px;font-weight:500;line-height:54px;width:640px}
.hero h1 strong{color:var(--green);font-weight:700}
.hero .price{position:absolute;left:88px;top:334px;font-size:22px;font-weight:300}
.btn-dark{position:absolute;left:88px;top:396px;width:150px;height:50px;background:var(--dark);color:var(--white);font-size:13px;font-weight:600;display:flex;align-items:center;justify-content:center;gap:10px}
.hero .mouse{position:absolute;left:88px;top:556px}

/* presentation */
.presentation .visual{position:absolute;left:88px;top:772px;width:490px;height:530px;background:linear-gradient(150deg,#cfd3d8,#7d6a5c 60%,#3b2f2a)}
.section-title{font-size:48px;font-weight:400;line-height:54px}
.section-title b{font-weight:700}
.presentation .section-title{position:absolute;left:668px;top:970px}
.presentation .rule{position:absolute;left:624px;top:1098px;width:92px;height:4px;background:var(--green)}
.presentation p{position:absolute;left:671px;top:1118px;width:440px;font-size:15px;line-height:27px;color:#555;font-weight:300}

/* facilities */
.center-head{position:absolute;left:0;width:1200px;text-align:center}
.center-head .rule{width:50px;height:3px;background:var(--green);margin:14px auto 16px}
.center-head p{font-size:15px;font-weight:300;color:#555}
.dark-band{position:absolute;left:0;top:1809px;width:1200px;height:691px;background:var(--dark)}
.cards{position:absolute;left:88px;top:1548px;display:flex;gap:19px}
.card{width:242px;height:299px;background:var(--white);padding:40px 26px;box-shadow:0 8px 24px rgba(0,0,0,.06);position:relative}
.card h3{font-size:19px;font-weight:600;margin:22px 0 18px}
.card p{font-size:13px;line-height:22px;color:#777;font-weight:300}
.card .go{position:absolute;left:26px;bottom:30px}
.card.active{background:var(--green);color:var(--white)}
.card.active p{color:#eef7e2}

/* features */
.features .center-head{color:var(--white)}
.features .center-head p{color:#ddd}
.feature{position:absolute;width:420px;color:var(--white)}
.feature .num{position:absolute;left:0;top:-6px;font-size:30px;font-weight:700;color:#3a3536}
.feature h4{margin-left:32px;font-size:16px;font-weight:600}
.feature p{margin-left:32px;font-size:12px;line-height:21px;color:#c9c9c9;font-weight:300;margin-top:4px}

/* location */
.location .panel{position:absolute;left:88px;top:2613px;width:443px;height:392px;background:var(--green);color:var(--white);padding:26px 48px}
.location .panel h2{font-size:48px;font-weight:400;line-height:50px}
.location .panel h2 b{font-weight:700}
.location .panel p{font-size:14px;line-height:22px;margin-top:18px;width:320px;font-weight:300}
.location .map-frame{position:absolute;left:487px;top:2679px;width:631px;height:506px;background:var(--white);padding:10px;box-shadow:0 10px 30px rgba(0,0,0,.08)}
.location .map{width:100%;height:100%;background:linear-gradient(135deg,#e6e6e6,#d6d6d6)}

/* gallery */
.gallery-grid{position:absolute;left:206px;top:3432px;display:flex;gap:12px}
.shot{width:255px;height:348px;position:relative;color:var(--white)}
.shot .date{position:absolute;left:36px;bottom:32px;font-size:14px;font-weight:500}
.shot .view{position:absolute;left:144px;bottom:26px;font-size:22px;font-weight:700;color:var(--green)}

/* footer */
.site-footer{position:absolute;left:0;top:3872px;width:1200px;height:596px;background:var(--light)}
.site-footer .brand{position:absolute;left:88px;top:130px;font-size:26px;line-height:30px}
.site-footer .intro{position:absolute;left:88px;top:184px;width:300px;font-size:14px;line-height:22px;color:#555;font-weight:300}
.contact-item{position:absolute;left:88px;display:flex;gap:10px;font-size:13px;line-height:20px;color:#444}
.contact-item b{color:var(--ink);font-weight:600;display:block}
.socials{position:absolute;left:90px;top:448px;display:flex;gap:8px}
.socials i{width:26px;height:26px;border-radius:50%;display:block}
.form-title{position:absolute;left:546px;top:94px;font-size:46px;font-weight:400;line-height:52px}
.form-title b{font-weight:700}
.field{position:absolute}
.field label{display:block;font-size:12px;font-weight:500;line-height:16px;margin-bottom:6px}
.field .input{background:var(--white);border:1px solid var(--line);height:40px;font-size:12px;color:#999;padding:11px 16px}
.submit{position:absolute;left:546px;top:390px;width:125px;height:40px;background:var(--green);color:var(--white);font-size:13px;font-weight:600;display:flex;align-items:center;justify-content:center;letter-spacing:1px}
.site-footer .divider{position:absolute;left:88px;top:527px;width:1022px;height:1px;background:#d8d8d8}
.copyright{position:absolute;left:0;top:552px;width:1200px;text-align:center;font-size:13px;font-weight:500}
.to-top{position:absolute;left:1131px;top:503px;width:48px;height:48px;border-radius:50%;background:var(--green);display:flex;align-items:center;justify-content:center}
</style>
</head>
<body>

<header class="site-header">
  <div class="brand"><span class="mark"></span>GREEN CREST</div>
  <nav class="main-nav">
    <span>Green Crest</span><span>The Project</span><span>Apartments</span><span>Sales</span><span>Location</span><span>Gallery</span>
    <span class="cta">Contact</span>
    <span class="lang"><i></i>ENG ▾</span>
  </nav>
</header>

<section class="hero">
  <div class="accent"></div>
  <div class="photo" role="img" aria-label="Photo of a white residential tower with green balcony accents and trees"></div>
  <h1>Sale Of Apartments Directly From The investor with <strong>10% discount</strong></h1>
  <div class="price">Price from XXX EUR/m2</div>
  <div class="btn-dark">BUY NOW
    <svg width="16" height="10" viewBox="0 0 16 10"><path d="M0 5h14M10 1l4 4-4 4" fill="none" stroke="#fff" stroke-width="1.5"/></svg>
  </div>
  <svg class="mouse" width="20" height="32" viewBox="0 0 20 32"><rect x="1" y="1" width="18" height="30" rx="9" fill="none" stroke="#222" stroke-width="2"/><line x1="10" y1="7" x2="10" y2="13" stroke="#222" stroke-width="2"/></svg>
</section>

<section class="presentation">
  <div class="visual" role="img" aria-label="Architectural composition of glass and brick towers with white building silhouettes"></div>
  <h2 class="section-title">Project<br><b>Presentation</b></h2>
  <div class="rule"></div>
  <p>Architecture, building materials – facades, roof, common areas etc.), information board (assignor, contractor, etc.), maintenance and management info, level of completion, etc.</p>
</section>

<section class="facilities">
  <div class="center-head" style="top:1398px">
    <h2 class="section-title">Facilities/<b>Benefits</b></h2>
    <div class="rule"></div>
    <p>Table with all apartments (70) – unit, floor, entrance/block, typology (1 bed, 2 beds, etc),</p>
  </div>
  <div class="dark-band"></div>
  <div class="cards">
    <div class="card">
      <svg width="66" height="60" viewBox="0 0 66 60" fill="none" stroke="#222" stroke-width="2"><path d="M4 22L33 4l29 18v34H4z"/><rect x="16" y="28" width="34" height="20" rx="3"/><path d="M20 28l4-8h18l4 8"/><circle cx="23" cy="40" r="2"/><circle cx="43" cy="40" r="2"/></svg>
      <h3>Parking spaces</h3>
      <p>Etiam rhoncus maecenas cus tempus tellus ui condim entum rhon cus...</p>
      <svg class="go" width="20" height="10" viewBox="0 0 20 10"><path d="M0 5h18M14 1l4 4-4 4" fill="none" stroke="#999" stroke-width="1.3"/></svg>
    </div>
    <div class="card">
      <svg width="76" height="60" viewBox="0 0 76 60" fill="none" stroke="#222" stroke-width="2"><path d="M40 4v30M54 4v30M40 12h14M40 22h14"/><path d="M4 38c10-6 20 6 34 0s24-6 34 0"/><path d="M10 46c10 8 40 10 56-2" stroke="#8dc63f"/></svg>
      <h3>Pool</h3>
      <p>Etiam rhoncus maecenas cus tempus tellus ui condim entum rhon cus...</p>
      <svg class="go" width="20" height="10" viewBox="0 0 20 10"><path d="M0 5h18M14 1l4 4-4 4" fill="none" stroke="#999" stroke-width="1.3"/></svg>
    </div>
    <div class="card">
      <svg width="70" height="60" viewBox="0 0 70 60" fill="none" stroke="#222" stroke-width="2"><rect x="4" y="2" width="22" height="24" rx="2"/><path d="M11 20V8h6a4 4 0 010 8h-6"/><path d="M15 26v30"/><circle cx="30" cy="48" r="9"/><circle cx="58" cy="48" r="9"/><path d="M30 48l10-14h14l4 14M40 34l8 14"/></svg>
      <h3>Bicycle parking</h3>
      <p>Etiam rhoncus maecenas cus tempus tellus ui condim entum rhon cus...</p>
      <svg class="go" width="20" height="10" viewBox="0 0 20 10"><path d="M0 5h18M14 1l4 4-4 4" fill="none" stroke="#999" stroke-width="1.3"/></svg>
    </div>
    <div class="card active">
      <svg width="70" height="60" viewBox="0 0 70 60" fill="none" stroke="#fff" stroke-width="2"><circle cx="35" cy="8" r="3"/><path d="M12 34a23 23 0 0146 0zM8 38h54"/><path d="M6 48l14-6h20l10 4-18 8H6"/></svg>
      <h3>Restaurant</h3>
      <p>Etiam rhoncus maecenas cus tempus tellus ui condim entum rhon cus...</p>
      <svg class="go" width="20" height="10" viewBox="0 0 20 10"><path d="M0 5h18M14 1l4 4-4 4" fill="none" stroke="#fff" stroke-width="1.3"/></svg>
    </div>
  </div>
</section>

<section class="features">
  <div class="center-head" style="top:1934px">
    <h2 class="section-title">Construction/<b>Features</b></h2>
    <div class="rule"></div>
    <p>Etiam rhoncus maecenas tempus tellus eget condim entum rhon cus sem quam semper</p>
  </div>
  <div class="feature" style="left:147px;top:2087px"><span class="num">1</span><h4>Rovena Windows</h4><p>5 chamber noise reducing glazing with high temperature and noise insulation efficiency</p></div>
  <div class="feature" style="left:147px;top:2177px"><span class="num">2</span><h4>Vellberg bricks</h4><p>Austrian Vellberg Poroline bricks with porous system and 25 cm thick outer walls</p></div>
  <div class="feature" style="left:147px;top:2267px"><span class="num">3</span><h4>High Ceilings</h4><p>2.70m high ceilings giving the light and space you need</p></div>
  <div class="feature" style="left:147px;top:2357px"><span class="num">4</span><h4>Thermal Insulation</h4><p>System Bramet – Bramet Silicone Plaster Thermal Insulation System 10 cm thick and 15 cm thick from the north walls</p></div>
  <div class="feature" style="left:607px;top:2087px"><span class="num">5</span><h4>Air conditioners</h4><p>All air conditioners piping systems are installed – ready to plug in the inside and outside body of the aircon system</p></div>
  <div class="feature" style="left:607px;top:2177px"><span class="num">6</span><h4>HPL ventilated facede</h4><p>Fasadex GmbH – Suspended ventilated facade with highly pressed laminated panels by Fasadex GmbH in wood color</p></div>
  <div class="feature" style="left:607px;top:2267px"><span class="num">7</span><h4>Panoramic Aurelo lifts</h4><p>Overlooking the park – Giving you the everyday glimpse over the inside garden and putting a smile on your face</p></div>
  <div class="feature" style="left:607px;top:2357px"><span class="num">8</span><h4>Waterproofing with PVC</h4><p>Membrane Tekora – PVC membrane with high puncture and tear resistance, UV resistance and vapor permeability</p></div>
</section>

<section class="location">
  <div class="panel">
    <h2>Our<br><b>Location</b></h2>
    <p>Neighborhood, local attractions, metro/bus stops, schools nearby, big shops etc.Maybe some sort of infographic with distance to the POI above.</p>
  </div>
  <div class="map-frame"><div class="map" role="img" aria-label="Street map of the neighbourhood around the building"></div></div>
</section>

<section class="gallery">
  <div class="center-head" style="top:3295px">
    <h2 class="section-title">Our/<b>Gallery</b></h2>
    <div class="rule"></div>
    <p>Boxes for each month with photos of the construction progress</p>
  </div>
  <div class="gallery-grid">
    <div class="shot" role="img" aria-label="Construction progress photo of balconies" style="background:linear-gradient(160deg,#4b5a72,#2b2f38)"><span class="date">April 2021</span><span class="view">View</span></div>
    <div class="shot" role="img" aria-label="Construction progress photo of a street with towers" style="background:linear-gradient(160deg,#8aa0b2,#6f7d64 60%,#3f4440)"><span class="date">April 2021</span><span class="view">View</span></div>
    <div class="shot" role="img" aria-label="Construction progress photo of glass towers" style="background:linear-gradient(160deg,#6d7f99,#2f4d73 60%,#3a3f45)"><span class="date">April 2021</span><span class="view">View</span></div>
  </div>
</section>

<footer class="site-footer">
  <div class="brand"><span class="mark"></span>GREEN CREST</div>
  <p class="intro">Please select a topic below related to your inquiry. If you don't find what you need, fill out our contact form</p>
  <div class="contact-item" style="top:262px">
    <svg width="14" height="18" viewBox="0 0 14 18"><path d="M7 1a6 6 0 016 6c0 4-6 10-6 10S1 11 1 7a6 6 0 016-6z" fill="none" stroke="#8dc63f" stroke-width="2"/><circle cx="7" cy="7" r="2" fill="#8dc63f"/></svg>
    <div><b>Location*</b>Some address goes here city<br>name country name</div>
  </div>
  <div class="contact-item" style="top:334px">
    <svg width="14" height="16" viewBox="0 0 14 16"><path d="M2 1h3l2 4-2 2a9 9 0 004 4l2-2 3 2v3c-7 0-13-6-13-13z" fill="#8dc63f"/></svg>
    <div><b>Phone*</b>Call Us +00 555 010 2040</div>
  </div>
  <div class="contact-item" style="top:386px">
    <svg width="15" height="12" viewBox="0 0 15 12"><rect width="15" height="12" rx="1" fill="#8dc63f"/><path d="M1 2l6.5 5L14 2" fill="none" stroke="#fff" stroke-width="1.3"/></svg>
    <div><b>Email*</b>info@greencrest.com</div>
  </div>
  <div class="socials"><i style="background:#3b5998"></i><i style="background:#1da1f2"></i></div>

  <h2 class="form-title">Contact <b>Form</b></h2>
  <div class="field" style="left:546px;top:166px;width:182px"><label>Name*</label><div class="input">Enter your name</div></div>
  <div class="field" style="left:737px;top:166px;width:182px"><label>Email*</label><div class="input">Enter your email</div></div>
  <div class="field" style="left:928px;top:166px;width:182px"><label>Phone*</label><div class="input">Enter your phone</div></div>
  <div class="field" style="left:546px;top:239px;width:564px"><label>Message*</label><div class="input" style="height:110px">Type your text</div></div>
  <div class="submit">SUBMIT</div>
  <div class="divider"></div>
  <div class="to-top"><svg width="12" height="14" viewBox="0 0 12 14"><path d="M6 13V2M1 6l5-5 5 5" fill="none" stroke="#fff" stroke-width="1.5"/></svg></div>
  <div class="copyright">© Copyright 2021 Green Crest All Rights Reserved</div>
</footer>

</body>
</html>
```